Volbrey Inc Business Card

Looking to get an updated business card for a Contract Machining company (www.volbreyinc.example) - looking for a clean design the portrays the technical nature of the business - colors can follow the website design and be in any combination that makes sense (red black, white, metallic or silver) - logos attached for use also. Would like space for: Name, title, business phone (555 214-3086), cell phone , website (www.volbreyinc.example) - possibly QR code could be integrated for website (designer choice), business address - 418 Harlow Bend, Ostenmere, LK 48199 (cards will be for 4 employees, I will either need to modify a template or I can provide individual information)
Target Market(s)
Aerospace, defense and medical device manufacturing companies that need machining
Industry/Entity Type
Machining for aerospace, defense, medical
Contact Information for Business Card
Name, Title, Business Phone, Cell Phone, email, business website and business address
Look and feel

```html
<!DOCTYPE html>
<html lang="en">
<head>
<meta charset="utf-8">
<title>Volbrey Inc Business Card</title>
<link rel="stylesheet" href="https://fonts.googleapis.com/css2?family=Montserrat:wght@400;700;800&display=swap">
<style>
  :root {
    --backdrop: #d2d2d2;
    --card-white: #f1f1ef;
    --brand-red: #b0141b;
    --brand-red-deep: #9e1016;
    --ink-gray: #6f6f6f;
    --rule-gray: #d6d6d3;
  }
  * { box-sizing: border-box; margin: 0; padding: 0; }
  html, body {
    width: 1200px; height: 1051px; overflow: hidden;
    background: var(--backdrop);
    font-family: "Montserrat", Arial, sans-serif;
  }
  .card-stage {
    position: relative; width: 1200px; height: 1051px;
    display: flex; align-items: center; justify-content: center; gap: 48px;
  }
  .card {
    width: 525px; height: 300px; border-radius: 3px;
    box-shadow: 0 14px 30px rgba(0,0,0,0.18);
    position: relative; overflow: hidden;
  }
  .card-front {
    background: var(--card-white);
    display: flex; align-items: center;
    padding: 0 34px;
    border-bottom: 3px solid var(--brand-red);
  }
  .brand-block {
    width: 180px; display: flex; flex-direction: column; align-items: center; gap: 14px;
  }
  .brand-mark {
    width: 96px; height: 96px; border-radius: 50%;
    background: var(--brand-red);
  }
  .brand-name {
    color: var(--brand-red); font-weight: 800; font-size: 22px; letter-spacing: 0.5px;
    text-transform: uppercase; white-space: nowrap;
  }
  .divider {
    width: 1px; height: 190px; background: var(--rule-gray); margin: 0 28px 0 18px;
  }
  .contact-block { color: var(--ink-gray); font-size: 12px; line-height: 1.5; }
  .person-name {
    color: var(--brand-red); font-weight: 700; font-size: 19px;
    text-transform: uppercase; letter-spacing: 0.3px; line-height: 1.1;
  }
  .person-title { font-size: 12.5px; margin-bottom: 16px; }
  .address { margin-bottom: 14px; }
  .contact-line { display: flex; align-items: center; gap: 8px; white-space: nowrap; }
  .contact-line svg { width: 10px; height: 10px; fill: var(--brand-red); flex: none; }
  .card-back {
    background: var(--brand-red);
    background-image: linear-gradient(160deg, var(--brand-red) 0%, var(--brand-red-deep) 100%);
    display: flex; flex-direction: column; align-items: center; justify-content: center; gap: 14px;
  }
  .back-mark {
    width: 92px; height: 92px; border-radius: 50%; background: var(--card-white);
  }
  .back-name {
    color: var(--card-white); font-weight: 800; font-size: 20px; letter-spacing: 0.5px;
    text-transform: uppercase;
  }
</style>
</head>
<body>
<main class="card-stage">
  <section class="card card-front">
    <div class="brand-block">
      <div class="brand-mark"></div>
      <div class="brand-name">Volbrey Inc</div>
    </div>
    <div class="divider"></div>
    <div class="contact-block">
      <div class="person-name">Marcus Tolland</div>
      <div class="person-title">President</div>
      <div class="address">418 Harlow Bend<br>Ostenmere, LK 48199</div>
      <div class="contact-line">
        <svg viewBox="0 0 10 10"><path d="M2 0.5 L3.6 0.5 L4.2 3 L3 3.8 Q4 6 6.2 7 L7 5.8 L9.5 6.4 L9.5 8 Q9.5 9.5 8 9.5 Q0.5 9 0.5 2 Q0.5 0.5 2 0.5 Z"/></svg>
        <span>555 214-3086</span>
      </div>
      <div class="contact-line">
        <svg viewBox="0 0 10 10"><path d="M0.5 2 L9.5 2 L9.5 8 L0.5 8 Z M1 2.5 L5 5.5 L9 2.5" stroke="#f1f1ef" stroke-width="0.8"/></svg>
        <span>m.tolland@volbreyinc.example</span>
      </div>
      <div class="contact-line">
        <svg viewBox="0 0 10 10"><circle cx="5" cy="5" r="4.5"/><path d="M0.5 5 H9.5 M5 0.5 Q2.5 5 5 9.5 M5 0.5 Q7.5 5 5 9.5" stroke="#f1f1ef" stroke-width="0.6" fill="none"/></svg>
        <span>www.volbreyinc.example</span>
      </div>
    </div>
  </section>
  <section class="card card-back">
    <div class="back-mark"></div>
    <div class="back-name">Volbrey Inc</div>
  </section>
</main>
</body>
</html>
```